Roofing Contractor business card redesign

I want to redesign my business card with a fresh, eye catching concept

Target Market(s)

Residential Roofing Clients, potential employees, and subcontractors.

Industry/Entity Type

Business

Colors

Designer to choose colors to be used in the design.

Requirements
Nice to have
• I just want something that's more pleasing to the eye. You can use a combination of either / or of my logos.

```html
<!DOCTYPE html>
<html lang="en">
<head>
<meta charset="utf-8">
<title>Fair Hands General Contractors – Business Card</title>
<link href="https://fonts.googleapis.com/css2?family=Roboto:wght@400;700;900&display=swap" rel="stylesheet">
<style>
  :root {
    --backdrop: #e9e4dd;
    --card-dark: #3d2020;
    --card-light: #fbfbfa;
    --brand-maroon: #5b1c1c;
    --ring-cream: #f4efe8;
    --text-light: #ffffff;
    --text-muted: #eadfdc;
    --text-grey: #6d6868;
    --illus-orange: #e8782a;
    --illus-yellow: #f3c63a;
  }
  * { box-sizing: border-box; margin: 0; padding: 0; }
  html, body { width: 1200px; height: 911px; overflow: hidden; }
  body {
    background: var(--backdrop);
    font-family: "Roboto", sans-serif;
    position: relative;
  }
  .card {
    position: absolute;
    top: 301px;
    width: 540px;
    height: 308px;
    border-radius: 22px;
    overflow: hidden;
    box-shadow: 0 14px 30px rgba(60, 40, 30, 0.28);
  }
  .card--front { left: 40px; background: var(--card-dark); color: var(--text-light); }
  .card--back { left: 620px; background: var(--card-light); }

  /* front */
  .emblem {
    position: absolute;
    right: 28px;
    top: 18px;
    width: 272px;
    height: 272px;
    border-radius: 50%;
    background: var(--ring-cream);
    padding: 9px;
  }
  .emblem__art {
    width: 100%;
    height: 100%;
    border-radius: 50%;
    background:
      radial-gradient(circle at 60% 55%, var(--illus-orange) 0 30%, transparent 55%),
      radial-gradient(circle at 30% 30%, var(--illus-yellow) 0 20%, transparent 50%),
      var(--card-dark);
  }
  .identity { position: absolute; left: 30px; top: 70px; }
  .identity__name { font-weight: 700; font-size: 19px; letter-spacing: 0.3px; text-transform: uppercase; }
  .identity__role { font-size: 14px; line-height: 1.35; color: var(--text-muted); }
  .address { position: absolute; left: 30px; top: 158px; font-size: 13.5px; line-height: 1.35; color: var(--text-muted); }
  .contacts { position: absolute; left: 30px; top: 204px; list-style: none; font-size: 13.5px; line-height: 1.42; color: var(--text-muted); }
  .contacts li { display: flex; align-items: center; gap: 9px; }
  .contacts svg { width: 12px; height: 12px; flex: none; }

  /* back */
  .logo {
    position: absolute;
    left: 0; right: 0; top: 92px;
    display: flex; flex-direction: column; align-items: center;
    color: var(--brand-maroon);
    font-weight: 900;
  }
  .logo__row { display: flex; align-items: center; gap: 10px; }
  .logo__name { font-size: 46px; letter-spacing: -0.5px; line-height: 1; }
  .logo__dot { width: 38px; height: 38px; border-radius: 50%; background: var(--brand-maroon); }
  .logo__tagline { font-size: 19px; margin-top: 4px; line-height: 1; }
  .website {
    position: absolute; left: 0; right: 0; bottom: 52px;
    text-align: center; font-size: 13px; letter-spacing: 7px; color: var(--text-grey);
  }
</style>
</head>
<body>
  <section class="card card--front">
    <div class="emblem">
      <div class="emblem__art" role="img" aria-label="Illustration of three roofing workers with tools inside a circular badge"></div>
    </div>
    <div class="identity">
      <p class="identity__name">Dale Morrow</p>
      <p class="identity__role">Keller Certified Roof Inspector</p>
      <p class="identity__role">Licensed Property Adjuster</p>
    </div>
    <p class="address">4810 Cedar Ridge Drive Suite 118<br>Plano, TX 75093</p>
    <ul class="contacts">
      <li>
        <svg viewBox="0 0 12 12" aria-hidden="true"><path d="M2.5 1l2 2-1 1.5c.7 1.5 1.8 2.6 3.3 3.3L8.3 6.8l2 2L9 10.5C5 10 2 7 1.5 3z" fill="currentColor"/></svg>
        (555) 214-3800
      </li>
      <li>
        <svg viewBox="0 0 12 12" aria-hidden="true"><rect x="1.5" y="2" width="9" height="8" fill="none" stroke="currentColor" stroke-width="1.3"/></svg>
        (555) 306-7142
      </li>
      <li>
        <svg viewBox="0 0 12 12" aria-hidden="true"><rect x="1" y="2.5" width="10" height="7" fill="none" stroke="currentColor" stroke-width="1.2"/><path d="M1 2.5l5 4 5-4" fill="none" stroke="currentColor" stroke-width="1.2"/></svg>
        dale@fairhandstx.com
      </li>
      <li>
        <svg viewBox="0 0 12 12" aria-hidden="true"><circle cx="6" cy="6" r="5" fill="currentColor"/></svg>
        www.fairhandstx.com
      </li>
    </ul>
  </section>

  <section class="card card--back">
    <div class="logo">
      <div class="logo__row">
        <span class="logo__name">Fair Hands</span>
        <span class="logo__dot"></span>
      </div>
      <span class="logo__tagline">General Contractors, Inc.</span>
    </div>
    <p class="website">www.fairhandstx.com</p>
  </section>
</body>
</html>
```